SaaS / Consulting / Solution website redesign

We need a website design that:
- Is completely different than our current design : https://plumvessel.net
- Has a very minimal amount of copy
- Changes our positioning from a SaaS application to a solutions company. Solutions company means that we help our customers solve their problems with consulting, training, and tools. An example of a solutions company is here: https://oldpages.example/web/20130111103320/http://www.brindlework.com:80/
- Does not make us look like a start up
- Is more people oriented than technology oriented

We need a designer that:
- Is a rebel at heart
- Is a minimalist
- Tells us why our current site sucks
- Can disagree with us
- Can also do copywriting or already has a copywriter that can help
- Is ok with saying we have capability that we don't in order to see if people actually want that
- Can understand the difference between our grand vision and where we need to focus ourselves today in order to get there

Who we are:
- Entrepreneurs
- Programmers
- Consultants
- Investors

Here's our design goals:
#1 Get customers, investors, employers, and partners excited about our unique and clearly articulated value proposition
#2 Get people to contact us asking for help with their programs
#3 Position ourselves as an expert in the skills based volunteering, mentorship, and group collaboration
#4 Make it easy for people, who already know who we are, to register online

What our grand vision is:
- Create a marketplace where any person can go to our site and find time with anyone they need to meet with. Whether that is their hair stylist, school advisor, parent of your kids class, dentist, attorney, etc.

What will you get if you win:
- In addition to the prize of this project we will have many landing pages and other revisions we will need in the future. We currently don't have a designer or copywriter and need to add that capability to our team

Who do we need to appeal to:
- Directors that are launching innovative programs inside organizations
- IT personnel who are trying to disqualify our technology so they don't have to support it or deal with it when it doesn't go well
- Enterprise IT architects who don't want our product being on its own island within their organization totally incompatible with everything else. Architects which are trying to assess how our platform will co-exist with all their other platforms
- Vice Presidents who want to help their directors understand that we don't have enough experience to help them
- Program managers who have to juggle a million things and need a tool that actually helps instead of confuses them and adds more work for them.
- Program managers & directors that have been given ambiguous goals by their board of directors like "improve retention, increase engagement, create innovation, get people to collaborate." And who have no idea where to start or how to deliver on things like that.
- Program managers, directors, and vice presidents that are trying to understand how our technology and services fit into their existing technology and capability
- Employees who are bored and uninspired with their current tools and are hoping for some excitement in their life. Kind of like candy or a double espresso.
- Investors who think, our company like all the rest, are going to waste their money and make them look like a fool

Other information:
-The CSS and html needs to be responsive

-Our registration onboarding flow needs to collect this information:
User first name
user last name
user email
(verify their email)
user phone number
(verify their phone number)
User profile image (optional)
User profile summary (optional, like a bio, freeform text fiels)
If applicable: Register their organization
Organization name
Organization image (optional)
Account Mailing address
account Billing address (could be same as mailing address)
account Billing email address (could be same as user address)
account Product selection (pricing tier)
account Credit card information

The designs I am getting are a good start but they are only the front page. I just want you to know that I am expecting and need more than a landing page to complete the design. I will likely need a page that outlines the benefits and features of the product itself, how its different than our competitors, which will not be on the front page. I will need a registration flow. I will need a blog page design so we can post blog articles, I will need a team page, a page that goes into detail on our training, our services. I will likely need a page that shows all news and media we have been in. I need to show customer and user quotes, case studies, a way to contact us, partners, general resources like on collaboration, product tutorials, customers. I need the site to address a comprehensive set of needs. I need that design to be consistent and thorough. I know what PlateHarbor is. I'm not using because I need more than a template that was customized. I need to be unique and match our brand thoughtfully, beautifully, and artistically. Someone asked me a question about how Murmly is similar to our tool in the way it is referred by end users and purchased by managers. Our website needs to primarily talk to the managers as I explained in the brief but it needs to appear cool and exciting to our end-users without focusing on the technology too much. Murmly is a tool that teams use to collaborate in small and large enterprises. The value prop for them is that communication is easier. But they don't put that on their website. Why? Because the users of the technology won't go to the website to find out information on it, they get their information from someone who is using it and demos it to them. When Ines tells her manager Otto "Lets get murmly, Ruth is using it at her company and its great" Ines's manager doesn't know anything about murmly so she promptly googles it. The most important thing from Ines's perspective is that Otto agrees to try it out. Otto's biggest concern is that productivity will be enhanced to degraded. Murmly knows this and so on the front page they know they are talking to Otto NOT Ines because Ines is already sold on it and doesn't need to get sold on the website. Ines is end user. Otto is the purchaser. We have the same problem and so our end users are not the ones purchasing our product, their managers are purchasing our product. We get referred by our end users and vetted by their managers. Hope this helps! Thank you for looking at this project!  Added Wednesday, June 7, 2017

Another observation I am having about the designs being submitted. I believe we used the animations on our current website because animations / cartoons connect with the "inner child" in our users. Whatever that means :-). I think it's what makes our brand fun. I have a hard time imagining that we could make the design fun looking without animations but I'm sure it can be achieved. I also recognize that blending pictures of real people and animations is hard. So either we must masterfully blend them, use only animations, or make the real people have a LOT of fun! So far most of the designs while achieve the goal of appealing to the serious Vice Presidents and directors, they are not doing a good job at appealing to the overworked program managers and bored employees. There seems to stand another challenge with animations which is animations are hard to find and/or create that achieve the message / emotion we are trying to communicate. I don't have any good answers for this but I will say we can hire both animators and illustrators if we need to. All you have to do is communicate the effect in the website design with some simpler version maybe not the end illustration or animation itself. Added Wednesday, June 7, 2017

• Sex appeal and a sense of humor. Copy that makes people excited and clairvoyant about our potential.
• Boring renditions of other non-inspiring websites

```html
<!DOCTYPE html>
<html lang="en">
<head>
<meta charset="utf-8">
<title>Plumvessel — Team</title>
<link rel="stylesheet" href="https://fonts.googleapis.com/css2?family=Roboto:wght@300;400;500;700&display=swap">
<style>
  :root {
    --blue: #3fb3e5;
    --blue-deep: #16a6ee;
    --green: #7cc57c;
    --ink: #222;
    --muted: #666;
    --line: #dcdcdc;
    --band: #ececec;
    --footer: #eef0f4;
    --white: #fff;
    --avatar-bg: #d6f0fb;
    --avatar-ring: #e6eef2;
  }
  * { box-sizing: border-box; margin: 0; padding: 0; }
  html, body { width: 682px; height: 1200px; overflow: hidden; }
  body { position: relative; background: var(--white); font-family: "Roboto", Arial, sans-serif; color: var(--ink); }
  a { text-decoration: none; }
  .abs { position: absolute; }

  /* Header */
  .brand { font-weight: 500; color: var(--ink); font-size: 13px; letter-spacing: .2px; }
  .site-brand { left: 92px; top: 28px; }
  .main-nav a { position: absolute; top: 31px; font-size: 6px; color: #8a8a8a; }
  .main-nav a.is-active { color: var(--blue-deep); }
  .btn { position: absolute; font-size: 6.5px; font-weight: 500; color: var(--white); display: flex; align-items: center; justify-content: center; }
  .btn-login { left: 495px; top: 25px; width: 38px; height: 17px; background: var(--green); }
  .btn-register { left: 537px; top: 25px; width: 55px; height: 17px; background: var(--blue-deep); }

  /* Hero */
  .hero { left: 0; top: 54px; width: 682px; height: 93px; background: linear-gradient(100deg, #3cb1e4, #45b6e6 60%, #3aaee2); }
  .hero-title { left: 150px; top: 90px; color: var(--white); font-weight: 300; font-size: 27px; letter-spacing: .5px; }

  /* Breadcrumb bar */
  .crumbs { left: 91px; top: 158px; font-size: 5.6px; color: var(--ink); }
  .crumbs span { color: var(--blue); }
  .search { left: 478px; top: 153px; width: 98px; height: 17px; border: 1px solid #cfcfcf; font-size: 7px; color: #444; padding: 4px; }
  .search-icon { left: 580px; top: 157px; }
  .rule { left: 91px; top: 175px; width: 500px; height: 1px; background: var(--line); }

  /* Sections */
  .band { left: 0; top: 448px; width: 682px; height: 310px; background: var(--band); }
  .section-title { left: 0; width: 682px; text-align: center; font-weight: 300; font-size: 25px; letter-spacing: .6px; color: #111; }

  .lead-avatar { width: 86px; height: 86px; border-radius: 50%; background: radial-gradient(circle at 50% 60%, #9ccbe2 0%, var(--avatar-bg) 70%); border: 2px solid var(--avatar-ring); }
  .lead-name { font-size: 7.5px; font-weight: 400; color: var(--ink); }
  .lead-bio { font-size: 5.5px; line-height: 7px; color: var(--muted); width: 105px; margin-top: 3px; }
  .socials { display: flex; gap: 6px; margin-top: 6px; }
  .social-dot { width: 4px; height: 4px; border-radius: 50%; background: #777; }

  .member { display: flex; align-items: center; gap: 5px; }
  .member-badge { width: 31px; height: 31px; border-radius: 50%; background: var(--blue); display: flex; align-items: center; justify-content: center; border: 1px solid #35a3d4; }
  .member-badge i { width: 12px; height: 12px; border-radius: 50%; border: 1px solid #2a7fa8; }
  .member-name { font-size: 7.6px; font-weight: 400; color: var(--ink); }
  .member .socials { margin-top: 3px; }

  /* Footer */
  .site-footer { left: 0; top: 1031px; width: 682px; height: 169px; background: var(--footer); }
  .footer-brand { left: 91px; top: 1066px; }
  .footer-text { left: 91px; top: 1096px; width: 260px; font-size: 5.6px; line-height: 10px; color: #333; }
  .btn-ghost { position: absolute; font-size: 5.4px; font-weight: 700; letter-spacing: .3px; display: flex; align-items: center; justify-content: center; }
  .btn-demo { left: 97px; top: 1132px; width: 57px; height: 15px; background: var(--blue-deep); color: var(--white); }
  .btn-brochure { left: 158px; top: 1132px; width: 79px; height: 15px; background: var(--white); color: var(--blue-deep); }
  .footer-links a { position: absolute; top: 1096px; font-size: 5.4px; color: #555; letter-spacing: .2px; }
  .email-field { left: 432px; top: 1133px; width: 108px; height: 13px; border-bottom: 1px solid #d6d9de; font-size: 5px; color: #c9ccd2; padding-top: 4px; }
  .btn-subscribe { left: 545px; top: 1132px; width: 45px; height: 15px; background: var(--white); color: var(--blue-deep); }
  .footer-rule { left: 91px; top: 1169px; width: 500px; height: 1px; background: #d9dce1; }
  .legal { left: 92px; top: 1181px; font-size: 5.4px; color: #444; }
  .legal-links a { position: absolute; top: 1181px; font-size: 5.4px; color: #444; }
  .footer-social { position: absolute; top: 1178px; width: 5px; height: 5px; border-radius: 50%; background: #666; }
</style>
</head>
<body>

<header>
  <div class="abs brand site-brand">Plumvessel</div>
  <nav class="main-nav">
    <a class="is-active" href="#" style="left:270px">Home</a>
    <a href="#" style="left:306px">Product</a>
    <a href="#" style="left:348px">About</a>
    <a href="#" style="left:385px">Library</a>
    <a href="#" style="left:424px">Careers</a>
    <a href="#" style="left:466px">Contact</a>
  </nav>
  <a class="btn btn-login" href="#">Login</a>
  <a class="btn btn-register" href="#">Register Now</a>
</header>

<div class="abs hero" role="img" aria-label="Blue banner with a faint network-of-dots backdrop"></div>
<h1 class="abs hero-title">TEAM</h1>

<div class="abs crumbs">Home &gt; <span>Team</span></div>
<div class="abs search">Search Site</div>
<svg class="abs search-icon" width="9" height="9" viewBox="0 0 9 9" aria-hidden="true"><circle cx="3.5" cy="3.5" r="2.5" fill="none" stroke="#7cc57c" stroke-width="1.2"/><line x1="5.3" y1="5.3" x2="8.3" y2="8.3" stroke="#7cc57c" stroke-width="1.4"/></svg>
<div class="abs rule"></div>

<!-- Founders -->
<h2 class="abs section-title" style="top:205px">FOUNDERS</h2>

<div class="abs lead-avatar" style="left:121px;top:263px" role="img" aria-label="Illustrated portrait of John Doe"></div>
<div class="abs" style="left:215px;top:283px">
  <div class="lead-name">John Doe:</div>
  <p class="lead-bio">Lorem Ipsum has been the industry's standard dummy text ever since the 1500s.</p>
  <div class="socials"><span class="social-dot"></span><span class="social-dot"></span></div>
</div>
<div class="abs lead-avatar" style="left:365px;top:263px" role="img" aria-label="Illustrated portrait of Alice Doe"></div>
<div class="abs" style="left:459px;top:283px">
  <div class="lead-name">Alice Doe:</div>
  <p class="lead-bio">Lorem Ipsum has been the industry's standard dummy text ever since the 1500s.</p>
  <div class="socials"><span class="social-dot"></span><span class="social-dot"></span></div>
</div>

<div class="abs member" style="left:195px;top:381px"><span class="member-badge"><i></i></span><div><div class="member-name">Craig Murphy</div><div class="socials"><span class="social-dot"></span><span class="social-dot"></span></div></div></div>
<div class="abs member" style="left:309px;top:381px"><span class="member-badge"><i></i></span><div><div class="member-name">Rob Phil</div><div class="socials"><span class="social-dot"></span><span class="social-dot"></span></div></div></div>
<div class="abs member" style="left:412px;top:381px"><span class="member-badge"><i></i></span><div><div class="member-name">Helen Price</div><div class="socials"><span class="social-dot"></span><span class="social-dot"></span></div></div></div>

<!-- Team members -->
<div class="abs band"></div>
<h2 class="abs section-title" style="top:475px">TEAM MEMBERS</h2>

<div class="abs lead-avatar" style="left:121px;top:530px" role="img" aria-label="Illustrated portrait of John Doe"></div>
<div class="abs" style="left:215px;top:550px">
  <div class="lead-name">John Doe:</div>
  <p class="lead-bio">Lorem Ipsum has been the industry's standard dummy text ever since the 1500s.</p>
  <div class="socials"><span class="social-dot"></span><span class="social-dot"></span></div>
</div>
<div class="abs lead-avatar" style="left:365px;top:530px" role="img" aria-label="Illustrated portrait of Alice Doe"></div>
<div class="abs" style="left:459px;top:550px">
  <div class="lead-name">Alice Doe:</div>
  <p class="lead-bio">Lorem Ipsum has been the industry's standard dummy text ever since the 1500s.</p>
  <div class="socials"><span class="social-dot"></span><span class="social-dot"></span></div>
</div>

<div class="abs member" style="left:143px;top:647px"><span class="member-badge"><i></i></span><div><div class="member-name">Craig Murphy</div><div class="socials"><span class="social-dot"></span><span class="social-dot"></span></div></div></div>
<div class="abs member" style="left:257px;top:647px"><span class="member-badge"><i></i></span><div><div class="member-name">Rob Phil</div><div class="socials"><span class="social-dot"></span><span class="social-dot"></span></div></div></div>
<div class="abs member" style="left:361px;top:647px"><span class="member-badge"><i></i></span><div><div class="member-name">Helen Price</div><div class="socials"><span class="social-dot"></span><span class="social-dot"></span></div></div></div>
<div class="abs member" style="left:465px;top:647px"><span class="member-badge"><i></i></span><div><div class="member-name">Stephen</div><div class="socials"><span class="social-dot"></span><span class="social-dot"></span></div></div></div>
<div class="abs member" style="left:143px;top:690px"><span class="member-badge"><i></i></span><div><div class="member-name">Craig Paul</div><div class="socials"><span class="social-dot"></span><span class="social-dot"></span></div></div></div>
<div class="abs member" style="left:257px;top:690px"><span class="member-badge"><i></i></span><div><div class="member-name">Murphy</div><div class="socials"><span class="social-dot"></span><span class="social-dot"></span></div></div></div>
<div class="abs member" style="left:361px;top:690px"><span class="member-badge"><i></i></span><div><div class="member-name">Mickle</div><div class="socials"><span class="social-dot"></span><span class="social-dot"></span></div></div></div>
<div class="abs member" style="left:465px;top:690px"><span class="member-badge"><i></i></span><div><div class="member-name">Helen Price</div><div class="socials"><span class="social-dot"></span><span class="social-dot"></span></div></div></div>

<!-- Advisors -->
<h2 class="abs section-title" style="top:786px">ADVISORS</h2>

<div class="abs lead-avatar" style="left:243px;top:840px" role="img" aria-label="Illustrated portrait of John Doe"></div>
<div class="abs" style="left:338px;top:860px">
  <div class="lead-name">John Doe:</div>
  <p class="lead-bio">Lorem Ipsum has been the industry's standard dummy text ever since the 1500s.</p>
  <div class="socials"><span class="social-dot"></span><span class="social-dot"></span></div>
</div>

<div class="abs member" style="left:252px;top:958px"><span class="member-badge"><i></i></span><div><div class="member-name">Craig Murphy</div><div class="socials"><span class="social-dot"></span><span class="social-dot"></span></div></div></div>
<div class="abs member" style="left:366px;top:958px"><span class="member-badge"><i></i></span><div><div class="member-name">Rob Phil</div><div class="socials"><span class="social-dot"></span><span class="social-dot"></span></div></div></div>

<!-- Footer -->
<footer>
  <div class="abs site-footer"></div>
  <div class="abs brand footer-brand">Plumvessel</div>
  <p class="abs footer-text">Lorem Ipsum is simply dummy text of the printing and typesetting industry. Lorem Ipsum has been the industry's standard dummy text ever since the 1500s</p>
  <a class="btn-ghost btn-demo" href="#">REQUEST DEMO</a>
  <a class="btn-ghost btn-brochure" href="#">DOWNLOAD BROCHURE</a>
  <nav class="footer-links">
    <a href="#" style="left:436px">CONTACT</a>
    <a href="#" style="left:498px">ABOUT</a>
    <a href="#" style="left:550px">IMPRESSUM</a>
  </nav>
  <div class="abs email-field">YOUR@EMAIL.COM</div>
  <a class="btn-ghost btn-subscribe" href="#">SUBSCRIBE</a>
  <div class="abs footer-rule"></div>
  <p class="abs legal">© 2017 Plumvessel Inc All rights reserved | Plumvessel® is a registered trademark of Plumvessel Inc</p>
  <nav class="legal-links">
    <a href="#" style="left:368px">Blog</a>
    <a href="#" style="left:399px">Press</a>
  </nav>
  <span class="footer-social" style="left:538px"></span>
  <span class="footer-social" style="left:561px"></span>
  <span class="footer-social" style="left:584px"></span>
</footer>

</body>
</html>
```